Business Card: RW Office Partners - Your organised problem solver

Business Name: RW Office Partners
Website: www.rwofficepartners.com.au
Email: marisol@rwofficepartners.com.au
Mobile: 61 482 907 236
Facebook: @rwofficepartners
Instrgram: @rwofficepartners

Brading Colours:
HEX
#986474
#ddccd3
#7a8498
#c9d8e4
#000000
#ffffff

Tag Line: Your organised problem solver

Link to DRAFT website:
https://deskhelpcollective.wixsite.com/rw-office-partners

About Page from the website:
My name is Marisol Wrenfield, and I would love to assist you to become more productive in your day to day and achieve your business and personal goals.
My mission is to give you time, time to work on the important tasks of your business or to be able to spend more time with your family. I will take on the tasks you don’t have time for, don’t know well or simply don’t like to do.
I have an extensive background in Administration, Tender Coordination, Document Control, WHS and Quality Management working primarily in the Construction, Mining and Corporate World.
I am passionate about being organised, having order and making things in your life (and mine) easier! I love to watch something unfold and grow into something amazing! I am known for being the go-to problem solver, the organiser of all things, producing high standards of work even under pressure. I’m also a confident communicator, and I understand that you’re busy running your business.

Target Market(s)

Small to Medium Business who require assistance in their business by a virtual assistant.

Industry/Entity Type

Virtual Assistant

Contact Information for Business Card

Mobile: 61 482 907 236

Font styles to use
Sans Serif

Colors
ffffff

Requirements
Must have
• Branding Colours as outlined.
Contact Details as outlined.
Logo as provided.
Proper contact details - mobile, facebook, instragm, website.
Simple, Elegant, very clean looking.
Should not have
• Note cute with pictures.
Not too girly as still want to market to construction companies.

```html
<!DOCTYPE html>
<html lang="en">
<head>
<meta charset="utf-8">
<title>RW Office Partners – Business Card</title>
<link href="https://fonts.googleapis.com/css2?family=Roboto:wght@400;500;700&display=swap" rel="stylesheet">
<style>
  :root {
    --plum: #86495f;
    --plum-line: #7d3f55;
    --sky: #bfd1e0;
    --slate: #6f7a8e;
    --ink: #3a3f4b;
    --paper: #ffffff;
    --backdrop: #ecebe9;
  }
  html, body {
    margin: 0;
    width: 1200px;
    height: 900px;
    overflow: hidden;
    background: var(--backdrop);
    font-family: "Roboto", Arial, sans-serif;
  }
  .canvas {
    position: relative;
    width: 1200px;
    height: 900px;
  }
  .card {
    position: absolute;
    left: 320px;
    width: 560px;
    height: 320px;
    background: var(--paper);
    box-shadow: 0 6px 18px rgba(0,0,0,0.16);
    overflow: hidden;
  }
  .card--front { top: 90px; }
  .card--back { top: 490px; }

  /* Front */
  .front__band {
    position: absolute;
    left: 0; right: 0;
    height: 78px;
    background: var(--sky);
  }
  .front__band--top { top: 0; }
  .front__band--bottom { bottom: 0; }
  .front__rule {
    position: absolute;
    left: 0; right: 0;
    height: 3px;
    background: var(--plum-line);
  }
  .front__rule--top { top: 78px; }
  .front__rule--bottom { bottom: 78px; }
  .front__brand {
    position: absolute;
    top: 81px; bottom: 81px;
    left: 0; right: 0;
    display: flex;
    flex-direction: column;
    align-items: center;
    justify-content: center;
    gap: 8px;
  }
  .brand-name {
    display: flex;
    align-items: center;
    gap: 10px;
    color: var(--plum);
    font-weight: 700;
    text-transform: uppercase;
    letter-spacing: 0.5px;
  }
  .brand-name__square {
    width: 14px;
    height: 14px;
    background: var(--plum);
  }
  .front__brand .brand-name { font-size: 27px; }
  .tagline {
    color: var(--slate);
    font-size: 11px;
    font-weight: 700;
    letter-spacing: 0.8px;
    text-transform: uppercase;
  }

  /* Back */
  .back__pattern {
    position: absolute;
    left: 0; right: 0;
    height: 58px;
    background: var(--plum);
  }
  .back__pattern--top { top: 0; }
  .back__pattern--bottom { bottom: 0; }
  .back__panel {
    position: absolute;
    top: 58px; bottom: 58px;
    left: 0; right: 0;
    display: flex;
    align-items: center;
    justify-content: space-between;
    padding: 0 36px 0 30px;
  }
  .contact-list {
    list-style: none;
    margin: 0;
    padding: 0;
    display: flex;
    flex-direction: column;
    gap: 9px;
    color: var(--ink);
    font-size: 12px;
  }
  .contact-list__item {
    display: flex;
    align-items: center;
    gap: 8px;
  }
  .contact-icon {
    width: 16px;
    height: 16px;
    flex: none;
  }
  .contact-list__item--split {
    gap: 26px;
  }
  .contact-list__pair {
    display: flex;
    align-items: center;
    gap: 6px;
  }
  .back__panel .brand-name { font-size: 17px; }
</style>
</head>
<body>
<main class="canvas">

  <section class="card card--front" aria-label="Business card front">
    <div class="front__band front__band--top"></div>
    <div class="front__rule front__rule--top"></div>
    <div class="front__brand">
      <div class="brand-name"><span class="brand-name__square"></span>RW Office Partners</div>
      <div class="tagline">Your organised problem solver</div>
    </div>
    <div class="front__rule front__rule--bottom"></div>
    <div class="front__band front__band--bottom"></div>
  </section>

  <section class="card card--back" aria-label="Business card back">
    <div class="back__pattern back__pattern--top" role="img" aria-label="Repeating monogram pattern in plum"></div>
    <div class="back__panel">
      <ul class="contact-list">
        <li class="contact-list__item">
          <svg class="contact-icon" viewBox="0 0 16 16" aria-hidden="true">
            <circle cx="8" cy="8" r="8" fill="var(--plum)"/>
            <rect x="4" y="5.2" width="8" height="5.6" fill="none" stroke="#fff" stroke-width="1"/>
            <path d="M4 5.4 L8 8.6 L12 5.4" fill="none" stroke="#fff" stroke-width="1"/>
          </svg>
          marisol@rwofficepartners.com.au
        </li>
        <li class="contact-list__item">
          <svg class="contact-icon" viewBox="0 0 16 16" aria-hidden="true">
            <circle cx="8" cy="8" r="8" fill="var(--plum)"/>
            <rect x="5.5" y="3.6" width="5" height="8.8" rx="0.8" fill="none" stroke="#fff" stroke-width="1"/>
            <circle cx="8" cy="11" r="0.6" fill="#fff"/>
          </svg>
          61 482 907 236
        </li>
        <li class="contact-list__item">
          <svg class="contact-icon" viewBox="0 0 16 16" aria-hidden="true">
            <circle cx="8" cy="8" r="8" fill="var(--plum)"/>
            <circle cx="8" cy="8" r="4.2" fill="none" stroke="#fff" stroke-width="0.9"/>
            <ellipse cx="8" cy="8" rx="1.8" ry="4.2" fill="none" stroke="#fff" stroke-width="0.9"/>
            <path d="M3.8 8 H12.2" stroke="#fff" stroke-width="0.9"/>
          </svg>
          www.rwofficepartners.com.au
        </li>
        <li class="contact-list__item contact-list__item--split">
          <span class="contact-list__pair">
            <svg class="contact-icon" viewBox="0 0 16 16" aria-hidden="true"><circle cx="8" cy="8" r="6" fill="var(--plum)"/></svg>
            @rwofficepartners
          </span>
          <span class="contact-list__pair">
            <svg class="contact-icon" viewBox="0 0 16 16" aria-hidden="true"><rect x="2" y="2" width="12" height="12" fill="var(--plum)"/></svg>
            @rwofficepartners
          </span>
        </li>
      </ul>
      <div class="brand-name"><span class="brand-name__square"></span>RW Office Partners</div>
    </div>
    <div class="back__pattern back__pattern--bottom" role="img" aria-label="Repeating monogram pattern in plum"></div>
  </section>

</main>
</body>
</html>
```